Fern Lattice Table & Chair Rentals

We need a business card for a table and chair rental company. We rent tables and chairs for weddings, funerals, business events and parties. We want something that looks clean and elegant while not being too busy. We would like colors in the green and blue hues and avoiding anything orange. We want to make sure the font is large enough to be seen easily.

Target Market(s)

Wedding & Event Rentals

Industry/Entity Type

Events

Contact Information for Business Card

Fern Lattice, sales@fernlatticerentals.com, fernlatticerentals.com, 360-555-0182

Requirements
Must have
• Easy to read font
Should not have
• Orange anywhere in the design

```html
<!DOCTYPE html>
<html lang="en">
<head>
<meta charset="utf-8">
<title>Fern Lattice Table &amp; Chair Rentals – Business Card</title>
<link rel="stylesheet" href="https://fonts.googleapis.com/css2?family=Exo+2:wght@400;500;600&family=PT+Sans:wght@400&display=swap">
<style>
  :root {
    --backdrop: #e6e6e6;
    --card: #ffffff;
    --ink: #2a2418;
    --accent: #2e8a67;
    --link: #2f6fa8;
    --shadow: rgba(0, 0, 0, 0.35);
  }
  * { box-sizing: border-box; margin: 0; padding: 0; }
  html, body {
    width: 1189px;
    height: 1200px;
    overflow: hidden;
    background: var(--backdrop);
  }
  body {
    position: relative;
    font-family: "Exo 2", sans-serif;
    color: var(--ink);
  }
  .card {
    position: absolute;
    left: 171px;
    width: 856px;
    height: 488px;
    background: var(--card);
    box-shadow: 6px 8px 12px var(--shadow);
  }
  .card--front { top: 67px; }
  .card--back { top: 625px; }

  .brand-name {
    font-family: "Exo 2", sans-serif;
    font-weight: 500;
    font-size: 54px;
    line-height: 1;
    color: var(--ink);
    letter-spacing: -0.5px;
  }
  .tagline {
    font-family: "PT Sans", sans-serif;
    font-size: 34px;
    line-height: 1;
    color: var(--ink);
    margin-top: 20px;
    padding-left: 6px;
    white-space: nowrap;
  }

  /* Front */
  .front-brand {
    position: absolute;
    right: 49px;
    top: 322px;
  }
  .front-bar {
    position: absolute;
    right: 0;
    top: 317px;
    width: 24px;
    height: 122px;
    background: var(--accent);
  }

  /* Back */
  .back-brand {
    position: absolute;
    left: 57px;
    top: 80px;
  }
  .hours {
    position: absolute;
    left: 556px;
    top: 66px;
    font-size: 25.5px;
    line-height: 30.5px;
    list-style: none;
  }
  .divider-row {
    position: absolute;
    left: 57px;
    right: 45px;
    top: 234px;
    height: 56px;
    display: flex;
    align-items: center;
    gap: 28px;
  }
  .divider-line {
    flex: 1;
    height: 2px;
    background: var(--accent);
  }
  .divider-name {
    font-size: 48px;
    font-weight: 500;
    line-height: 1;
    white-space: nowrap;
  }
  .back-bar {
    position: absolute;
    right: 0;
    top: 243px;
    width: 13px;
    height: 35px;
    background: var(--accent);
  }
  .contacts {
    position: absolute;
    left: 57px;
    top: 346px;
    list-style: none;
    font-size: 25px;
  }
  .contacts li {
    display: flex;
    align-items: center;
    height: 32.5px;
    gap: 12px;
  }
  .contact-icon {
    width: 24px;
    height: 24px;
    flex: none;
  }
  .web-domain { color: var(--link); }
  .location {
    position: absolute;
    right: 45px;
    top: 412px;
    font-size: 25px;
    line-height: 30px;
  }
</style>
</head>
<body>

  <section class="card card--front" aria-label="Card front">
    <div class="front-brand">
      <div class="brand-name">Fern Lattice</div>
      <div class="tagline">Table and Chair Rentals</div>
    </div>
    <div class="front-bar"></div>
  </section>

  <section class="card card--back" aria-label="Card back">
    <div class="back-brand">
      <div class="brand-name">Fern Lattice</div>
      <div class="tagline">Table and Chair Rentals</div>
    </div>

    <ul class="hours">
      <li>Mon-Fri: 8am to 6pm</li>
      <li>Saturday: 8am to 4pm</li>
      <li>Sunday: 9am to 1pm</li>
    </ul>

    <div class="divider-row">
      <div class="divider-line"></div>
      <div class="divider-name">Fern Lattice</div>
    </div>
    <div class="back-bar"></div>

    <ul class="contacts">
      <li>
        <svg class="contact-icon" viewBox="0 0 24 24" aria-hidden="true">
          <rect width="24" height="24" rx="4" fill="#2a2418"/>
          <path d="M8 5 l3 0 l1 4 l-2 1.5 q1 3 3.5 4.5 l1.5 -2 l4 1 l0 3 q-1 2 -3 2 q-6 -1 -9.5 -8 q-1 -3 1.5 -6z" fill="#fff"/>
        </svg>
        <span>360-555-0182</span>
      </li>
      <li>
        <svg class="contact-icon" viewBox="0 0 24 24" aria-hidden="true">
          <rect width="24" height="24" rx="4" fill="#2a2418"/>
          <rect x="4.5" y="7" width="15" height="10.5" fill="none" stroke="#fff" stroke-width="1.6"/>
          <path d="M4.5 7 L12 13 L19.5 7 M4.5 17.5 L10 12.5 M19.5 17.5 L14 12.5" fill="none" stroke="#fff" stroke-width="1.4"/>
        </svg>
        <span>sales@fernlatticerentals.com</span>
      </li>
      <li>
        <svg class="contact-icon" viewBox="0 0 24 24" aria-hidden="true">
          <rect width="24" height="24" rx="4" fill="#2a2418"/>
          <circle cx="12" cy="12" r="7" fill="none" stroke="#fff" stroke-width="1.4"/>
          <ellipse cx="12" cy="12" rx="3" ry="7" fill="none" stroke="#fff" stroke-width="1.2"/>
          <path d="M5 12 H19 M6.2 8.5 H17.8 M6.2 15.5 H17.8 M12 5 V19" stroke="#fff" stroke-width="1.1"/>
        </svg>
        <span>www.<span class="web-domain">fernlatticerentals</span>.com</span>
      </li>
    </ul>

    <p class="location">Alderport, Washington</p>
  </section>

</body>
</html>
```